UPDATE 2: I HAVE ATTACHED TWO PHOTOS; PLEASE CONSIDER USING EITHER ONE IN A NEW DESIGN. THANK YOU.
UPDATE: I HAVE INCLUDED 4 SAMPLE BOOK COVERS THAT I LIKE TO HELP YOU ORIENT YOUR DESIGN WORK
Looking for book cover, spine, and back for a MEMOIR. Details:
TITLE: Mama's Quiet Orchard
AUTHOR: Lorisha Pemberfeld
GENRE: Memoir
STYLE REQUESTED: Abstract and colorful; designers are welcome to get creative. Note that the memoir takes place largely in a poor African American city.
BOOK SUMMARY: As a young girl, Lorisha Pemberfeld—or “Rishi” to her friends and family—discovers the man she thought was her father wasn’t, and her real biological father wants little if anything to do with her. What follows is the story of a girl’s longing, a longing disturbed by abuse, disappointment, and loneliness.
Set against the backdrop of Gary, Indiana—the then “murder capital of the world”—Mama’s Quiet Orchard follows Lorisha as she searches and grows, following a path that eventually leads her to self-discovery and self-confidence.
Template provided for InDesign. Please note margins and bleed areas. Make sure any letters/words are at least one inch from edges. On spine, leave three inches at bottom for publisher's logo.
Updates
To all designers: Please note that there should NOT be any images of people as part of your designs. Thank you, and my apologies for not mentioning that in the initial ask.

```html
<!DOCTYPE html>
<html lang="en">
<head>
<meta charset="utf-8">
<title>Mama’s Quiet Orchard — Lorisha Pemberfeld</title>
<link rel="stylesheet" href="https://fonts.googleapis.com/css2?family=Jost:wght@400;500&family=Bodoni+Moda:wght@400&family=Mrs+Saint+Delafield&display=swap">
<style>
  :root {
    --ink: #ffffff;
    --red: #e0180f;
    --deep-red: #b80f0a;
    --orange: #f2561a;
    --gold: #f0a82a;
    --pink: #f2246a;
    --magenta: #d0289a;
    --violet: #7a3ad0;
    --blue: #5a55e0;
    --teal: #7fb8c0;
  }
  * { margin: 0; padding: 0; box-sizing: border-box; }
  html, body { width: 750px; height: 1200px; overflow: hidden; background: #fff; }
  .cover {
    position: relative;
    width: 750px;
    height: 1200px;
    overflow: hidden;
    color: var(--ink);
  }
  .cover__art { position: absolute; inset: 0; width: 100%; height: 100%; }
  .cover__content { position: absolute; inset: 0; }
  .genre {
    position: absolute;
    top: 196px;
    left: 0; right: 0;
    text-align: center;
    font-family: "Bodoni Moda", "Didot", serif;
    font-size: 70px;
    line-height: 1;
    letter-spacing: 1px;
  }
  .title-main {
    position: absolute;
    left: 0; right: 0;
    text-align: center;
    font-family: "Jost", "Futura", sans-serif;
    font-weight: 500;
    line-height: 1;
  }
  .title-main--top { top: 386px; font-size: 158px; letter-spacing: 2px; }
  .title-main--bottom { top: 642px; font-size: 134px; letter-spacing: 1px; }
  .title-connector {
    position: absolute;
    top: 535px;
    left: 0; right: 0;
    height: 100px;
  }
  .title-connector__rule { position: absolute; top: 0; left: 0; width: 750px; height: 100px; }
  .title-connector__word {
    position: absolute;
    top: 6px;
    left: 0; right: 0;
    text-align: center;
    font-family: "Mrs Saint Delafield", cursive;
    font-size: 96px;
    line-height: 1;
  }
  .divider {
    position: absolute;
    top: 886px;
    left: 239px;
    width: 273px;
    height: 2px;
    background: var(--ink);
  }
  .author {
    position: absolute;
    top: 928px;
    left: 0; right: 0;
    text-align: center;
    font-family: "Jost", "Futura", sans-serif;
    font-weight: 400;
    font-size: 45px;
    letter-spacing: 11px;
    line-height: 1;
  }
</style>
</head>
<body>
<main class="cover">
  <svg class="cover__art" viewBox="0 0 750 1200" preserveAspectRatio="none" role="img" aria-label="Abstract painted background with loose brushstrokes in red, orange, pink, magenta, violet and blue">
    <defs>
      <linearGradient id="base" x1="0" y1="0" x2="0" y2="1">
        <stop offset="0" stop-color="var(--red)"/>
        <stop offset="0.35" stop-color="var(--orange)"/>
        <stop offset="0.6" stop-color="var(--pink)"/>
        <stop offset="0.85" stop-color="var(--magenta)"/>
        <stop offset="1" stop-color="var(--pink)"/>
      </linearGradient>
      <radialGradient id="blueLeft" cx="0.05" cy="0.22" r="0.35">
        <stop offset="0" stop-color="var(--blue)" stop-opacity="0.95"/>
        <stop offset="1" stop-color="var(--blue)" stop-opacity="0"/>
      </radialGradient>
      <radialGradient id="goldMid" cx="0.75" cy="0.38" r="0.3">
        <stop offset="0" stop-color="var(--gold)" stop-opacity="0.8"/>
        <stop offset="1" stop-color="var(--gold)" stop-opacity="0"/>
      </radialGradient>
      <radialGradient id="tealMid" cx="0.45" cy="0.6" r="0.35">
        <stop offset="0" stop-color="var(--teal)" stop-opacity="0.7"/>
        <stop offset="1" stop-color="var(--teal)" stop-opacity="0"/>
      </radialGradient>
      <radialGradient id="violetRight" cx="0.95" cy="0.55" r="0.3">
        <stop offset="0" stop-color="var(--violet)" stop-opacity="0.7"/>
        <stop offset="1" stop-color="var(--violet)" stop-opacity="0"/>
      </radialGradient>
      <radialGradient id="violetBottom" cx="0.35" cy="0.88" r="0.35">
        <stop offset="0" stop-color="var(--violet)" stop-opacity="0.65"/>
        <stop offset="1" stop-color="var(--violet)" stop-opacity="0"/>
      </radialGradient>
      <radialGradient id="redTop" cx="0.4" cy="0.12" r="0.3">
        <stop offset="0" stop-color="var(--deep-red)" stop-opacity="0.8"/>
        <stop offset="1" stop-color="var(--deep-red)" stop-opacity="0"/>
      </radialGradient>
    </defs>
    <rect width="750" height="1200" fill="url(#base)"/>
    <rect width="750" height="1200" fill="url(#redTop)"/>
    <rect width="750" height="1200" fill="url(#blueLeft)"/>
    <rect width="750" height="1200" fill="url(#goldMid)"/>
    <rect width="750" height="1200" fill="url(#tealMid)"/>
    <rect width="750" height="1200" fill="url(#violetRight)"/>
    <rect width="750" height="1200" fill="url(#violetBottom)"/>
  </svg>

  <div class="cover__content">
    <p class="genre">A Memoir</p>
    <h1 class="title">
      <span class="title-main title-main--top">MAMA’S</span>
      <span class="title-connector">
        <svg class="title-connector__rule" viewBox="0 0 750 100" aria-hidden="true">
          <polygon points="114,50 258,46 258,54" fill="var(--ink)"/>
          <polygon points="637,50 493,46 493,54" fill="var(--ink)"/>
        </svg>
        <span class="title-connector__word">quiet</span>
      </span>
      <span class="title-main title-main--bottom">ORCHARD</span>
    </h1>
    <div class="divider"></div>
    <p class="author">LORISHA PEMBERFELD</p>
  </div>
</main>
</body>
</html>
```